Landscape design build company door flyer

I would like this flyer to convey a high-level of professionalism for a company that is excellent with communication with their clients as well as a company that does incredible installations

Went on vacation/holiday

```html
<!DOCTYPE html>
<html lang="en">
<head>
<meta charset="utf-8">
<title>Lotus Ridge Builders – Door Flyer</title>
<link href="https://fonts.googleapis.com/css2?family=Marcellus&family=Montserrat:wght@400;500;700;800&display=swap" rel="stylesheet">
<style>
  :root{
    --navy:#0e2b3a;
    --gold:#e6a910;
    --gold-deep:#d99a06;
    --white:#ffffff;
    --paper:#f1f1f1;
    --stage:#8fa5a3;
    --ink-soft:#dfe6ea;
  }
  *{box-sizing:border-box;margin:0;padding:0}
  html,body{width:1200px;height:960px;overflow:hidden;background:var(--stage)}
  .flyer{position:absolute;left:280px;top:29px;width:640px;height:902px;overflow:hidden;background:var(--navy);box-shadow:0 10px 30px rgba(0,0,0,.25)}
  .flyer__shapes{position:absolute;inset:0}
  .abs{position:absolute}
  .brand{left:0;width:324px;top:404px;text-align:center;color:var(--white)}
  .brand__name{font-family:"Marcellus",serif;font-size:25px;letter-spacing:.5px;line-height:1;display:flex;align-items:center;justify-content:center;gap:8px}
  .brand__mark{width:10px;height:10px;background:var(--white)}
  .brand__tag{font-family:"Montserrat",sans-serif;font-size:10.5px;font-weight:500;margin-top:6px;letter-spacing:.2px}
  .section-title{font-family:"Marcellus",serif;color:var(--gold);display:flex;align-items:center;gap:4px;line-height:1}
  .section-title::after{content:"";flex:1;height:1px;background:var(--gold)}
  .about__title{left:41px;top:472px;width:245px;font-size:17px}
  .about__text{left:41px;top:495px;width:245px;font-family:"Montserrat",sans-serif;font-size:9.4px;line-height:13.3px;color:var(--white);text-align:justify}
  .headline{left:322px;top:492px;font-family:"Marcellus",serif;color:var(--gold);font-size:32px;line-height:35px}
  .headline__sub{left:322px;top:570px;width:300px;font-family:"Montserrat",sans-serif;font-size:12.6px;line-height:17px;color:var(--white)}
  .thumb{top:649px;width:135px;height:108px;border:3px solid var(--white);box-shadow:0 5px 6px rgba(0,0,0,.35)}
  .thumb--pavilion{left:33px;background:linear-gradient(160deg,#9cb7c9 0%,#6b5a47 45%,#3a3a38 100%)}
  .thumb--garden{left:180px;background:linear-gradient(140deg,#556b4a 0%,#8a8f86 55%,#4e5a40 100%)}
  .thumb--deck{left:326px;background:linear-gradient(180deg,#6f7479 0%,#6f7479 30%,#5b3a2a 31%,#4a2e21 100%)}
  .thumb--aerial{left:473px;background:linear-gradient(180deg,#4d4f50 0%,#6d6a55 50%,#5d6066 100%)}
  .services__title{left:33px;top:777px;width:262px;font-size:18px;color:var(--navy)}
  .services__title::after{background:var(--navy)}
  .services__list{list-style:none;font-family:"Montserrat",sans-serif;font-size:11.5px;color:var(--navy);font-weight:500}
  .services__list li{display:flex;align-items:center;gap:6px;height:18.5px}
  .services__list li::before{content:"";width:10px;height:10px;border:1.5px solid var(--navy);background:var(--paper);flex:none}
  .services__list--a{left:33px;top:810px}
  .services__list--b{left:172px;top:809px}
  .cta__label{left:387px;top:801px;font-family:"Montserrat",sans-serif;font-weight:800;font-size:14px;color:var(--gold)}
  .cta__phone{left:385px;top:822px;font-family:"Montserrat",sans-serif;font-weight:800;font-size:24px;color:var(--navy);display:flex;align-items:center;gap:4px;letter-spacing:-.2px}
  .cta__phone svg{width:18px;height:18px}
  .cta__button{left:387px;top:862px;width:220px;height:24px;display:flex;font-family:"Montserrat",sans-serif;font-weight:800;font-size:14.5px;letter-spacing:.3px}
  .cta__button span{display:flex;align-items:center;justify-content:center}
  .cta__get{background:var(--gold);color:var(--white);width:68px}
  .cta__free{background:var(--navy);color:var(--white);flex:1}
</style>
</head>
<body>
<main class="flyer">
  <svg class="flyer__shapes" viewBox="0 0 640 902" width="640" height="902" aria-hidden="false">
    <defs>
      <linearGradient id="heroTone" x1="0" y1="0" x2="1" y2="1">
        <stop offset="0" stop-color="#c9c6bf"/>
        <stop offset=".35" stop-color="#5b5b5c"/>
        <stop offset=".6" stop-color="#b8865a"/>
        <stop offset="1" stop-color="#6b6f70"/>
      </linearGradient>
    </defs>
    <rect class="hero-photo" x="0" y="0" width="640" height="560" fill="url(#heroTone)" role="img" aria-label="Photo of a finished patio with stone retaining wall, planters and a live-edge wooden bench"/>
    <polygon fill="#e6a910" points="0,153 193,273 0,366"/>
    <polygon fill="#e6a910" points="0,366 193,268 640,516 640,713 0,713"/>
    <polygon fill="#0e2b3a" points="0,366 193,276 640,526 640,713 0,713"/>
    <rect x="0" y="713" width="640" height="189" fill="#e6a910"/>
    <polygon fill="#f1f1f1" points="369,784 640,784 640,902 326,902"/>
  </svg>

  <header class="brand abs">
    <div class="brand__name"><span class="brand__mark"></span>LOTUS RIDGE BUILDERS</div>
    <div class="brand__tag">OUTDOOR LIVING SPACES</div>
  </header>

  <h2 class="section-title about__title abs">ABOUT US</h2>
  <p class="about__text abs">Dean Marlow founded Lotus Ridge Builders in 2018. The company is a veteran-owned and operated hardscaping and landscaping design operation. Mr. Marlow faithfully served the greater Seattle area for more than two decades. Mr. Marlow wants to offer these many years of experience to build up each of Seattle’s exterior spaces to be the most beautiful, functional, and sustainable for both businesses and residents.</p>

  <h1 class="headline abs">It’s Time to<br>Discover Your Zen</h1>
  <p class="headline__sub abs">From vision to reality, let us bring your dream outdoor space to life.</p>

  <div class="thumb thumb--pavilion abs" role="img" aria-label="Photo of a covered outdoor pavilion with stone fireplace"></div>
  <div class="thumb thumb--garden abs" role="img" aria-label="Aerial photo of a terraced garden with paver walkway"></div>
  <div class="thumb thumb--deck abs" role="img" aria-label="Photo of composite deck boards meeting stone pavers"></div>
  <div class="thumb thumb--aerial abs" role="img" aria-label="Aerial photo of backyard landscaping between houses"></div>

  <h2 class="section-title services__title abs">Our Services</h2>
  <ul class="services__list services__list--a abs">
    <li>Pools</li><li>Paver Patios</li><li>Paver Driveways</li><li>Retaining Walls</li>
  </ul>
  <ul class="services__list services__list--b abs">
    <li>Decks &amp; Railings</li><li>Outdoor Lighting</li><li>Firepits and Fireplaces</li>
  </ul>

  <p class="cta__label abs">Call Us Now!</p>
  <p class="cta__phone abs">
    <svg viewBox="0 0 24 24" aria-hidden="true"><path fill="#0e2b3a" d="M6.6 10.8a15 15 0 0 0 6.6 6.6l2.2-2.2c.3-.3.7-.4 1-.2 1.1.4 2.3.6 3.6.6.6 0 1 .4 1 1V20c0 .6-.4 1-1 1A17 17 0 0 1 3 4c0-.6.4-1 1-1h3.5c.6 0 1 .4 1 1 0 1.3.2 2.5.6 3.6.1.3 0 .7-.2 1z"/></svg>
    (206) 555-0148
  </p>
  <div class="cta__button abs"><span class="cta__get">GET A</span><span class="cta__free">FREE ESTIMATE</span></div>
</main>
</body>
</html>
```